Banner for construction site to identify developer

we need a 4 foot by 8 foot banner to hang on the fence of a residential townhome development in Phoenix, Arizona that identifies Tolvane Holdings as the company behind the development/project. Also needs to include the logo, phone number, and web address. Would like to stick with the blue colors provided in the attached logo. The blues should stay the same but the letters in the logo can change to another color if necessary. Feel free to use "Tolvane Holdings" in place of "Tolvane Holdings Group". Looking for use of colors/design to take up space so banner is not just text with a logo.

Target Market(s)

drive by traffic looking at the site

Industry/Entity Type

Real Estate

Colors
0054AA
0677BA
7BADD7
CADEEF
E8F1F8

Requirements
Must have
• company name, phone number and web address

```html
<!DOCTYPE html>
<html lang="en">
<head>
<meta charset="utf-8">
<title>Tolvane Holdings – Site Banner</title>
<link rel="stylesheet" href="https://fonts.googleapis.com/css2?family=Open+Sans:wght@400;600;700&family=Poppins:wght@600&display=swap">
<style>
  :root {
    --blue-bright: #1ba1de;
    --blue-deep: #0677ba;
    --blue-navy: #1c6aa8;
    --ink: #3a3c40;
    --band: #38393d;
    --paper: #f7f8f9;
    --page: #ffffff;
  }
  * { box-sizing: border-box; margin: 0; padding: 0; }
  html, body {
    width: 852px;
    height: 1200px;
    overflow: hidden;
    background: var(--page);
  }
  .banner {
    position: absolute;
    left: 36px;
    top: 405px;
    width: 780px;
    height: 390px;
    background: var(--paper);
    box-shadow: 0 18px 40px rgba(0, 0, 0, 0.28);
    overflow: hidden;
    font-family: "Open Sans", Arial, sans-serif;
  }
  .banner-shapes {
    position: absolute;
    inset: 0;
  }
  .brand-lockup {
    position: absolute;
    left: 35px;
    top: 34px;
    display: flex;
    align-items: flex-start;
    gap: 10px;
  }
  .brand-lockup .brand-square {
    width: 40px;
    height: 40px;
    margin-top: 4px;
    background: var(--blue-bright);
  }
  .brand-lockup .brand-name {
    display: flex;
    flex-direction: column;
    align-items: flex-end;
    font-size: 24px;
    font-weight: 700;
    line-height: 1.05;
    color: var(--ink);
    letter-spacing: -0.3px;
  }
  .headline {
    position: absolute;
    left: 32px;
    top: 152px;
    font-size: 31px;
    font-weight: 700;
    letter-spacing: -0.5px;
    line-height: 1;
    white-space: nowrap;
  }
  .headline .first { color: var(--blue-bright); }
  .headline .second { color: var(--blue-navy); }
  .tagline {
    position: absolute;
    left: 34px;
    top: 214px;
    font-size: 22px;
    font-weight: 600;
    line-height: 1.3;
    color: var(--ink);
  }
  .phone {
    position: absolute;
    left: 34px;
    top: 330px;
    display: flex;
    align-items: center;
    gap: 16px;
    color: #fff;
    font-size: 31px;
    font-weight: 600;
    line-height: 1;
  }
  .phone svg { width: 28px; height: 28px; flex: none; }
  .web {
    position: absolute;
    left: 396px;
    width: 384px;
    top: 334px;
    text-align: center;
    font-family: "Poppins", Arial, sans-serif;
    font-weight: 600;
    font-size: 21px;
    color: var(--ink);
    line-height: 1;
  }
  .web .domain { color: var(--blue-navy); }
</style>
</head>
<body>
  <div class="banner">
    <svg class="banner-shapes" viewBox="0 0 780 390" width="780" height="390">
      <defs>
        <linearGradient id="project-photo-tone" x1="0" y1="0" x2="0" y2="1">
          <stop offset="0" stop-color="#4f93dc"/>
          <stop offset="0.35" stop-color="#9fbfe0"/>
          <stop offset="0.55" stop-color="#cdb894"/>
          <stop offset="0.8" stop-color="#5b5f6a"/>
          <stop offset="1" stop-color="#5e4f4c"/>
        </linearGradient>
      </defs>
      <polygon class="frame-stripe" points="318,0 780,0 780,310 442,310" fill="var(--blue-navy)"/>
      <polygon class="frame-gap" points="326,0 780,0 780,305 448,305" fill="var(--paper)"/>
      <polygon class="project-photo" role="img" aria-label="Photo of a modern multi-storey residential townhome building under a blue sky"
               points="332,0 780,0 780,302 454,302" fill="url(#project-photo-tone)"/>
      <polygon class="contact-band" points="0,307 356,307 378,390 0,390" fill="var(--band)"/>
      <polygon class="accent-stripe" points="362,307 372,307 396,381 780,381 780,390 386,390" fill="var(--blue-bright)"/>
    </svg>

    <div class="brand-lockup">
      <span class="brand-square"></span>
      <span class="brand-name"><span>Tolvane Holdings</span><span>Group</span></span>
    </div>

    <h1 class="headline"><span class="first">TOLVANE</span> <span class="second">HOLDINGS</span></h1>

    <p class="tagline">Crafting Phoenix's Premium<br>Residential Townhomes</p>

    <div class="phone">
      <svg viewBox="0 0 28 28" aria-hidden="true">
        <circle cx="14" cy="14" r="14" fill="var(--blue-bright)"/>
        <path d="M10.2 7.5c.6-.3 1.2 0 1.5.5l1.3 2.4c.3.6.2 1.2-.3 1.6l-1 .8c.7 1.6 2 2.9 3.6 3.6l.8-1c.4-.5 1-.6 1.6-.3l2.4 1.3c.5.3.8.9.5 1.5l-.6 1.2c-.4.8-1.3 1.2-2.2 1-4.4-1-7.9-4.5-8.9-8.9-.2-.9.2-1.8 1-2.2z" fill="var(--band)"/>
      </svg>
      <span>(480) 555-0147</span>
    </div>

    <p class="web">www.<span class="domain">tolvaneholdings</span>.com</p>
  </div>
</body>
</html>
```